cryotherapy business . Whole Body Cryotherapy, Localised Cryotherapy, Cryofacials

Need home page plus services, about, pricing, online booking, contact and blog page

I want something slick, hip and professional. Our studio colours are duck egg blue, white and grey

I would also like a social media scroll at the bottom of every page

I will upload some web designs that I like the look of

Target Market(s)

Men and Women 25-45

Industry/Entity Type

Health And Wellness

Coding

Coded - Design and coding required

Number of Pages Required

5+ page

Font styles to use
Serif
Sans Serif

Requirements
Must have
• Must be eye catching and easy to navigate
Nice to have
• animation
Should not have
• Not sure what the site should not have. I am fairly open to ideas as this is a brand new business.

```html
<!DOCTYPE html>
<html lang="en">
<head>
<meta charset="utf-8">
<title>Frostline – Cryotherapy Studio</title>
<link href="https://fonts.googleapis.com/css2?family=Lato:wght@400;700;900&family=Poppins:wght@300;400;500;600&display=swap" rel="stylesheet">
<style>
:root{
  --duck:#a9cfd9;
  --duck-dark:#8fbfcb;
  --duck-soft:#c9e1e8;
  --grey:#4d4d4d;
  --grey-mid:#7a7a7a;
  --text:#555;
  --heading:#3f3f3f;
  --footer:#121212;
  --white:#fff;
}
*{margin:0;padding:0;box-sizing:border-box}
html,body{width:1200px;height:4539px;overflow:hidden;background:var(--white)}
body{font-family:"Poppins",sans-serif;color:var(--text);position:relative}
.abs{position:absolute}
h1,h2,h3{font-family:"Lato",sans-serif}

/* header */
.logo{left:88px;top:22px;font-family:"Poppins",sans-serif;font-weight:300;font-size:52px;letter-spacing:6px;color:#8a8a8a;display:flex;align-items:center;gap:14px}
.logo .mark{width:14px;height:14px;border-radius:50%;background:var(--duck)}
.call{left:708px;top:24px;display:flex;align-items:center;gap:10px}
.call small{display:block;font-size:11px;color:#666}
.call strong{font-size:20px;color:#333;font-weight:600}
.quote{left:936px;top:24px;width:175px;height:42px;display:flex;font-size:15px;font-weight:600;color:#3e5a62}
.quote span{flex:1;background:var(--duck);display:flex;align-items:center;justify-content:center}
.quote i{width:46px;background:#7f9aa2;display:flex;align-items:center;justify-content:center}
.rule{left:0;top:93px;width:1200px;height:2px;background:#d8d8d8}
.nav{left:0;top:118px;width:1200px;display:flex;justify-content:center;gap:28px;font-size:16px;color:#333;font-weight:500}
.nav a{color:inherit;text-decoration:none;position:relative;padding-right:10px}
.nav a::after{content:"";position:absolute;right:0;bottom:2px;width:5px;height:5px;border-radius:50%;background:var(--duck)}

/* hero */
.hero{left:0;top:171px;width:1200px;height:631px;background:linear-gradient(180deg,#4f6f82 0%,#7d98a8 45%,#a9bcc6 75%,#6f8fa3 100%)}
.hero-title{left:0;top:355px;width:1200px;text-align:center;color:#fff}
.hero-title p{font-family:"Poppins",sans-serif;font-weight:300;font-size:60px;line-height:1}
.hero-title h1{font-weight:700;font-size:100px;line-height:1.05;letter-spacing:2px}
.arrow-btn{width:30px;height:30px;border-radius:50%;background:rgba(40,50,60,.55);display:flex;align-items:center;justify-content:center}

/* about */
.eyebrow{left:88px;top:906px;font-family:"Lato",sans-serif;font-size:26px;color:#8fb7c1;display:flex;align-items:center;gap:10px}
.eyebrow::after{content:"";width:76px;height:2px;background:#8fb7c1;display:inline-block;margin-top:14px}
.about-h{left:88px;top:950px;font-size:42px;font-weight:700;color:var(--heading)}
.about-p{left:90px;top:1012px;width:562px;font-size:14.5px;line-height:26px;text-align:justify;color:#666}
.about-p p+p{margin-top:14px}
.btn{display:flex;height:40px;font-size:15px;font-weight:600}
.btn span{display:flex;align-items:center;justify-content:center}
.read-about{left:89px;top:1254px;width:173px}
.read-about span:first-child{flex:1;background:var(--duck);color:#6e8f98}
.read-about span:last-child{width:45px;background:#7f9aa2;color:#fff}
.frame{border:8px solid var(--duck)}
.frame-tr{left:1003px;top:909px;width:105px;height:106px;border-left:0;border-bottom:0}
.frame-bl{left:761px;top:1187px;width:100px;height:100px;border-right:0;border-top:0}
.pod{left:806px;top:924px;width:272px;height:352px;background:linear-gradient(90deg,#e8eef2 0%,#2b49a8 30%,#1e3b97 55%,#dfe6ec 75%,#f3f5f7 100%);border-radius:18px 18px 6px 6px}

/* why */
.why{left:0;top:1395px;width:1200px;height:612px;background:linear-gradient(100deg,#b9d6de 0%,#a3c8d2 50%,#b5d3dc 100%)}
.why-frame-tr{left:343px;top:1503px;width:106px;height:48px;background:#4a4a4a}
.why-frame-bl{left:90px;top:1860px;width:48px;height:48px;background:#4a4a4a}
.why-img{left:100px;top:1513px;width:338px;height:385px;background:linear-gradient(90deg,#d8b489 0%,#4e6277 40%,#e9eef2 60%,#2a3242 100%)}
.why-h{left:534px;top:1494px;font-size:42px;font-weight:700;color:var(--heading)}
.why-body{left:536px;top:1558px;width:566px;font-size:14.5px;line-height:26px;color:#4e5f64;text-align:justify}
.why-list{list-style:none;margin-top:14px}
.why-list li{position:relative;padding-left:20px;margin-bottom:10px;line-height:30px}
.why-list li::before{content:"";position:absolute;left:2px;top:10px;border-left:9px solid #444;border-top:6px solid transparent;border-bottom:6px solid transparent}
.read-why{left:537px;top:1862px;width:175px}
.read-why span:first-child{flex:1;background:#4a4a4a;color:#fff}
.read-why span:last-child{width:45px;background:#2d2d2d;color:#fff}

/* services */
.sec-h{left:0;width:1200px;text-align:center;font-size:44px;font-weight:700;color:var(--heading)}
.card{top:2185px;width:327px;height:463px;padding:9px}
.card.dark{background:var(--grey);color:#fff}
.card.light{background:var(--duck);color:#444}
.card .ph{width:100%;height:209px}
.card h3{font-size:23px;font-weight:700;margin:26px 4px 14px}
.card p{font-size:14.5px;line-height:26px;text-align:justify;margin:0 4px}
.card .more{position:absolute;left:13px;top:420px;font-weight:600;font-size:15px}

/* pricing */
.pricing{left:0;top:2754px;width:1200px;height:590px;background:radial-gradient(ellipse at 78% 45%,#e0c0a4 0%,#c9a58a 18%,#3f7ec0 42%,#1c5fa8 70%,#2c73bb 100%)}
.price{background:#f4f5f6;border-radius:8px;text-align:center;color:#444;box-shadow:0 4px 14px rgba(0,0,0,.2)}
.price.mid{background:var(--duck)}
.price h3{font-family:"Poppins",sans-serif;font-weight:400;font-size:25px;line-height:29px;margin-top:20px}
.price .sub{font-size:13px;line-height:23px;margin:8px auto 0;width:140px;color:#555}
.price .amt{font-size:36px;font-weight:600;margin:18px 0 18px}
.price table{margin:0 auto;font-size:16px;border-collapse:collapse}
.price td{padding:2px 8px;text-align:left}
.price .book{display:inline-block;margin-top:30px;border:2px solid #3aa0d8;border-radius:20px;padding:7px 12px;font-size:13px;font-weight:500;background:#fff}
.price.mid .book{border-color:#555;background:transparent}

/* blog */
.post{top:3526px;width:327px}
.post .ph{width:327px;height:213px;border:4px solid #fff;box-shadow:0 2px 8px rgba(0,0,0,.15)}
.post .date{position:absolute;left:22px;top:200px;background:#bdbdbd;color:#fff;font-size:12px;padding:6px 22px}
.post h3{font-family:"Poppins",sans-serif;font-weight:500;font-size:22px;line-height:28px;color:#333;margin-top:66px}
.post p{font-size:13.5px;line-height:26px;color:#777;margin-top:14px;text-align:justify}
.post .rm{color:var(--duck-dark);font-size:15px;margin-top:14px;display:block}

/* footer */
.footer{left:0;top:4075px;width:1200px;height:464px;background:var(--footer);color:#fff}
.foot-h{font-family:"Lato",sans-serif;font-weight:700;font-size:26px}
.ci{display:flex;gap:16px;font-size:14px;line-height:22px;margin-top:16px}
.ci svg{flex:none;margin-top:2px}
.signup p{font-size:13px;line-height:24px;margin-top:18px;width:350px}
.field{margin-top:18px;width:410px;height:42px;background:#fff;border-radius:21px;display:flex;overflow:hidden}
.field span{flex:1;color:#888;font-size:13px;padding:12px 20px}
.field b{width:134px;background:var(--duck);color:#2f4d55;font-size:14px;font-weight:600;display:flex;align-items:center;justify-content:center;border-radius:21px}
.social{display:flex;gap:8px;margin-top:16px}
.social span{width:29px;height:29px;border:2px solid #fff;border-radius:50%;display:flex;align-items:center;justify-content:center}
.social span i{width:9px;height:9px;border-radius:50%;background:#fff}
.links{list-style:none;font-size:14px;line-height:29px;margin-top:10px;padding-left:8px}
.bottom-rule{left:0;top:4426px;width:1200px;height:1px;background:#2e2e2e}
.copy{left:0;top:4465px;width:1200px;text-align:center;font-size:15px;color:#fff}
</style>
</head>
<body>

<header>
  <div class="abs logo"><span>FROSTLINE</span><span class="mark"></span></div>
  <div class="abs call">
    <svg width="40" height="40" viewBox="0 0 40 40"><circle cx="20" cy="20" r="18" fill="none" stroke="#333" stroke-width="2"/><path d="M14 12c1-1 2-1 3 0l2 3c.5 1 0 2-1 2.5 1 2.5 3 4.5 5.5 5.5.5-1 1.5-1.5 2.5-1l3 2c1 1 1 2 0 3-2 2-5 2-8 0-4-2.5-7-6-8-9.5-.5-2 0-4 1-5.5z" fill="#333"/></svg>
    <div><small>Call Us Today</small><strong>555-014-2290</strong></div>
  </div>
  <div class="abs quote"><span>Get a Quote</span><i><svg width="18" height="8" viewBox="0 0 18 8"><path d="M0 4h15M12 1l4 3-4 3" stroke="#fff" stroke-width="1.5" fill="none"/></svg></i></div>
  <div class="abs rule"></div>
  <nav class="abs nav">
    <a>HOME</a><a>SERVICES</a><a>ABOUT</a><a>PRICING</a><a>ONLINE BOOKING</a><a>CONTACT &amp; BLOG</a>
  </nav>
</header>

<section>
  <div class="abs hero" role="img" aria-label="Man relaxing in an icy plunge pool surrounded by snow and ice"></div>
  <div class="abs arrow-btn" style="left:39px;top:451px"><svg width="10" height="10" viewBox="0 0 10 10"><path d="M6 2L3 5l3 3" stroke="#fff" stroke-width="1.6" fill="none"/></svg></div>
  <div class="abs arrow-btn" style="left:1131px;top:451px"><svg width="10" height="10" viewBox="0 0 10 10"><path d="M4 2l3 3-3 3" stroke="#fff" stroke-width="1.6" fill="none"/></svg></div>
  <div class="abs hero-title"><p>welcome to</p><h1>FROSTLINE</h1></div>
</section>

<section>
  <div class="abs eyebrow">About Us</div>
  <h2 class="abs about-h">WHAT IS CRYOTHERAPY?</h2>
  <div class="abs about-p">
    <p>Originally invented by doctors as a powerful anti-inflammatory tool, cryotherapy is a quick, noninvasive process that exposes your body to extreme cold of up to -250°F.</p>
    <p>This sudden drop in temperature increases circulation and pumps reoxygenated and nutrient enriched blood back into the bloodstream reducing pain &amp; inflammation and alleviating sore muscles. It's also known to release 'feel good' endorphins that help improve sleep, reduce stress, and increase your metabolism.</p>
  </div>
  <div class="abs btn read-about"><span>Read More</span><span>⟶</span></div>
  <div class="abs frame frame-tr"></div>
  <div class="abs frame frame-bl"></div>
  <div class="abs pod" role="img" aria-label="Whole body cryotherapy chamber with touchscreen panel"></div>
</section>

<section>
  <div class="abs why"></div>
  <div class="abs why-frame-tr"></div>
  <div class="abs why-frame-bl"></div>
  <div class="abs why-img" role="img" aria-label="Therapist opening a cryotherapy chamber for a client"></div>
  <h2 class="abs why-h">WHY FROSTLINE?</h2>
  <div class="abs why-body">
    <p>At Frostline, we believe that cryotherapy is one point on the wellness wheel. Our focus is to integrate cryotherapy into your recovery plan or as part of your health &amp; wellness regiment. Located inside Summit—Westbrook, CT's acclaimed physical therapy &amp; wellness center, our goal is to:</p>
    <ul class="why-list">
      <li>Understand your goals &amp; customize a treatment plan</li>
      <li>Collaborate, when appropriate, with healthcare professionals at Summit Physical Therapy &amp; Wellness to optimize treatment</li>
      <li>Monitor your progress over time</li>
    </ul>
  </div>
  <div class="abs btn read-why"><span>Read More</span><span>⟶</span></div>
</section>

<section>
  <h2 class="abs sec-h" style="top:2100px">OUR SERVICES</h2>
  <article class="abs card dark" style="left:90px">
    <div class="ph" role="img" aria-label="Client smiling inside a whole body cryotherapy chamber" style="background:linear-gradient(180deg,#4f86c6,#9fc3e6 60%,#c8cdd3)"></div>
    <h3>Whole Body Cryotherapy</h3>
    <p>Whole Body Cryotherapy is a quick, non-invasive process that exposes your body to extreme cold up to -250F. This sudden drop in temperature increases circulation</p>
    <span class="more">LEARN MORE</span>
  </article>
  <article class="abs card light" style="left:437px">
    <div class="ph" role="img" aria-label="Therapist applying localised cryotherapy to a client's shoulder" style="background:linear-gradient(90deg,#d9c1ad,#eef1f3 55%,#a9b4bd)"></div>
    <h3>Localised Cryotherapy</h3>
    <p>Local cryotherapy acts as a higher intensity, more efficient form of "icing." With the use of liquid nitrogen, the treatment delivers colder, more consistent temperatures</p>
    <span class="more">LEARN MORE</span>
  </article>
  <article class="abs card dark" style="left:783px">
    <div class="ph" role="img" aria-label="Client receiving a cryofacial with cold vapour" style="background:linear-gradient(180deg,#2c2f36,#8d9aa6 55%,#e5e9ec)"></div>
    <h3>Cryofacials</h3>
    <p>Cryo Facials apply pressurized liquid nitrogen vapors to the face, neck and scalp to help stimulate and improve the overall appearance of the skin. Regular treatments help stimulate</p>
    <span class="more">LEARN MORE</span>
  </article>
</section>

<section>
  <div class="abs pricing" role="img" aria-label="Smiling woman resting her chin on her hand against a blue background"></div>
  <div class="abs price" style="left:90px;top:2868px;width:204px;height:365px">
    <h3>Whole Body<br>Cryotherapy</h3>
    <div class="amt">$600</div>
    <table><tr><td>SINGLE</td><td>$40</td></tr><tr><td>10 PACK</td><td>$380</td></tr><tr><td>20 PACK</td><td>$720</td></tr><tr><td>MONTHLY*</td><td>$400</td></tr></table>
    <span class="book">BOOK A SESSION</span>
  </div>
  <div class="abs price" style="left:470px;top:2868px;width:203px;height:365px">
    <h3>Local<br>Cryotherapy</h3>
    <div class="amt">$600</div>
    <table><tr><td>SINGLE</td><td>$40</td></tr><tr><td>10 PACK</td><td>$380</td></tr><tr><td>20 PACK</td><td>$720</td></tr><tr><td>MONTHLY*</td><td>$400</td></tr></table>
    <span class="book">BOOK A SESSION</span>
  </div>
  <div class="abs price mid" style="left:282px;top:2833px;width:203px;height:427px">
    <h3>Cryo Facial</h3>
    <p class="sub">Cryo Facials apply pressurized liquid nitrogen</p>
    <div class="amt" style="margin:12px 0 14px">$600</div>
    <table><tr><td>SINGLE</td><td>$40</td></tr><tr><td>10 PACK</td><td>$380</td></tr><tr><td>20 PACK</td><td>$720</td></tr><tr><td>MONTHLY*</td><td>$400</td></tr></table>
    <span class="book" style="margin-top:26px">BOOK A SESSION</span>
  </div>
</section>

<section>
  <h2 class="abs sec-h" style="top:3438px;font-weight:400;font-family:'Poppins',sans-serif">Blog</h2>
  <article class="abs post" style="left:90px">
    <div class="ph" role="img" aria-label="Cryotherapy chamber with vapour and nitrogen tanks" style="background:linear-gradient(180deg,#6e6a66,#a9a7a3 60%,#4b4a48)"></div>
    <span class="date">▦ MAY 28, 2019</span>
    <h3>Lorem ipsum dolor<br>sit amet, consectetur</h3>
    <p>Sed ut perspiciatis unde omnis iste natus error sit voluptatem accusantium doloremque laudantium,</p>
    <span class="rm">Read More</span>
  </article>
  <article class="abs post" style="left:436px">
    <div class="ph" role="img" aria-label="Woman receiving a cryofacial treatment" style="background:linear-gradient(135deg,#e8d3c4,#c7d6e4 50%,#3a63b0)"></div>
    <span class="date">▦ MAY 23, 2019</span>
    <h3>Lorem ipsum dolor<br>sit amet, consectetur</h3>
    <p>Sed ut perspiciatis unde omnis iste natus error sit voluptatem accusantium doloremque laudantium,</p>
    <span class="rm">Read More</span>
  </article>
  <article class="abs post" style="left:782px">
    <div class="ph" role="img" aria-label="Laughing woman inside a cryotherapy chamber with blue light" style="background:linear-gradient(180deg,#2a3fa8,#4e7fd6 55%,#c9dcf2)"></div>
    <span class="date">▦ MAY 23, 2019</span>
    <h3>Lorem ipsum dolor<br>sit amet, consectetur</h3>
    <p>Sed ut perspiciatis unde omnis iste natus error sit voluptatem accusantium doloremque laudantium,</p>
    <span class="rm">Read More</span>
  </article>
</section>

<footer>
  <div class="abs footer"></div>
  <div class="abs" style="left:88px;top:4160px;color:#fff">
    <h3 class="foot-h">CONTACT US</h3>
    <div class="ci"><svg width="20" height="22" viewBox="0 0 20 22"><path d="M10 1a7 7 0 0 1 7 7c0 5-7 13-7 13S3 13 3 8a7 7 0 0 1 7-7z" fill="none" stroke="#fff" stroke-width="1.5"/><circle cx="10" cy="8" r="2.5" fill="none" stroke="#fff" stroke-width="1.5"/></svg><div>18 Glacier Row,<br>Easton, CT 06612</div></div>
    <div class="ci"><svg width="20" height="20" viewBox="0 0 20 20"><path d="M4 2c1-1 2-1 3 0l2 3c.5 1 0 2-1 2.5 1 2.5 3 4.5 5.5 5.5.5-1 1.5-1.5 2.5-1l3 2c1 1 1 2 0 3-2 2-5 2-8 0-4-2.5-7-6-8-9.5C2.5 5.5 3 3.5 4 2z" fill="none" stroke="#fff" stroke-width="1.3"/></svg><div>Phone :<br>555-014-2290</div></div>
    <div class="ci"><svg width="20" height="16" viewBox="0 0 20 16"><rect x="1" y="2" width="18" height="12" fill="none" stroke="#fff" stroke-width="1.4"/><path d="M1 2l9 7 9-7" fill="none" stroke="#fff" stroke-width="1.4"/></svg><div>Email :<br>hello@frostline-studio.com</div></div>
  </div>
  <div class="abs signup" style="left:450px;top:4156px;color:#fff">
    <h3 class="foot-h">SIGN UP TO RECEIVE EMAIL</h3>
    <p>Excepteur sint occaecat cupidatat non proident, sunt in culpa qui Nemo enim ipsam voluptatem</p>
    <div class="field"><span>Enter Email</span><b>SUBSCRIBE</b></div>
    <div class="social" aria-label="Social media links"><span><i></i></span><span><i></i></span><span><i></i></span><span><i></i></span></div>
  </div>
  <div class="abs" style="left:922px;top:4156px;color:#fff">
    <h3 class="foot-h">QUICK LINKS</h3>
    <ul class="links"><li>Home</li><li>Services</li><li>About</li><li>Pricing</li><li>Online Booking</li><li>Contact &amp; Blog</li></ul>
  </div>
  <div class="abs bottom-rule"></div>
  <div class="abs copy">Copyright © frostline 2019. All rights reserved. | Privacy Policy</div>
</footer>

</body>
</html>
```